Retail Jewelry Business Card Design Project

We are in need of a new business card design for a retail jewelry store. This store is in the business of fine jewelry including but not specific to bridal jewelry, diamonds, designer jewelry and watches.

This store has been in business for 20 years but continues to strive for a modern professional appeal. The main colors use for this business are a royal blue, white and silver.

Target Market(s)

Target market is ages 18-50

Industry/Entity Type

Jewelry

Requirements
Must have
• Sales Person Name
Sales Person Email Address

Store Address
Store Phone
Website

Standard business card size. No odd shapes or sizes.
Nice to have
• Overall modern feel for card.

We have thought that a design with a nice feature of the logo on the back of the card would be nice but open to ideas.
Should not have
• No specific images of jewelry should be used.

```html
<!DOCTYPE html>
<html lang="en">
<head>
<meta charset="utf-8">
<title>Harbor Lane Fine Jewelry – Business Card</title>
<link rel="stylesheet" href="https://fonts.googleapis.com/css2?family=Tinos:wght@400;700&family=Dancing+Script:wght@700&display=swap">
<style>
  :root {
    --royal: #2e3192;
    --lavender: #7a76b8;
    --white: #ffffff;
    --ink: #3f3f46;
    --rule: #b9b9c4;
    --backdrop: #e8e9ee;
  }
  * { box-sizing: border-box; margin: 0; padding: 0; }
  html, body { width: 1200px; height: 980px; overflow: hidden; }
  body {
    background: var(--backdrop);
    font-family: "Tinos", "Times New Roman", serif;
    position: relative;
  }
  .card {
    position: absolute;
    width: 760px;
    height: 434px;
    border-radius: 36px;
    overflow: hidden;
    box-shadow: 0 10px 24px rgba(40, 40, 70, 0.18);
  }
  .card--back {
    left: 400px; top: 50px;
    background: var(--royal);
    color: var(--white);
  }
  .card--front {
    left: 40px; top: 506px;
    background: var(--white);
    color: var(--ink);
  }
  .brand {
    position: absolute;
    text-align: center;
    font-weight: 700;
    line-height: 1;
  }
  .brand__name { display: block; font-size: 68px; letter-spacing: 1px; }
  .brand__line { display: block; font-size: 30px; letter-spacing: 6px; margin-top: 12px; }
  .card--back .brand { left: 0; right: 0; top: 120px; color: var(--white); }
  .card--front .brand { left: 120px; right: 60px; top: 42px; color: var(--royal); }
  .back__web {
    position: absolute; left: 0; right: 0; top: 290px;
    text-align: center;
    font-family: "Tinos", sans-serif;
    font-size: 20px;
    letter-spacing: 5px;
  }
  .swoosh { position: absolute; inset: 0; }
  .person {
    position: absolute; left: 170px; top: 200px;
    width: 240px;
  }
  .person__name {
    font-family: "Dancing Script", cursive;
    font-size: 28px;
    color: var(--royal);
    margin-bottom: 8px;
  }
  .person__address { font-size: 19px; line-height: 1.3; }
  .divider {
    position: absolute; left: 420px; top: 214px;
    width: 1px; height: 110px;
    background: var(--rule);
  }
  .contact {
    position: absolute; left: 440px; top: 214px;
    list-style: none;
    font-size: 19px;
  }
  .contact li { display: flex; align-items: center; gap: 10px; height: 34px; }
  .contact svg { width: 18px; height: 18px; flex: none; }
</style>
</head>
<body>

<section class="card card--back" aria-label="Card back">
  <div class="brand">
    <span class="brand__name">Harbor Lane</span>
    <span class="brand__line">FINE JEWELRY</span>
  </div>
  <p class="back__web">www.harborlanejewelry.com</p>
</section>

<section class="card card--front" aria-label="Card front">
  <svg class="swoosh" viewBox="0 0 760 434" preserveAspectRatio="none" aria-hidden="true">
    <path d="M0,250 C180,335 380,405 560,434 L0,434 Z" fill="var(--lavender)"/>
    <path d="M0,200 C170,285 360,375 500,434 L535,434 C375,385 185,300 0,232 Z" fill="var(--royal)"/>
    <path d="M0,360 C120,395 240,420 330,434 L0,434 Z" fill="var(--royal)"/>
  </svg>

  <div class="brand">
    <span class="brand__name">Harbor Lane</span>
    <span class="brand__line">FINE JEWELRY</span>
  </div>

  <div class="person">
    <p class="person__name">Martin Hale Corwin</p>
    <p class="person__address">2280 Bayview Street<br>Port Alder, FL 32499</p>
  </div>

  <div class="divider"></div>

  <ul class="contact">
    <li>
      <svg viewBox="0 0 18 18" aria-hidden="true"><circle cx="9" cy="9" r="8" fill="var(--royal)"/><path d="M6,5 l2,0 l0.6,2.2 l-1.2,0.8 a6,6 0 0 0 2.6,2.6 l0.8,-1.2 l2.2,0.6 l0,2 a7,7 0 0 1 -7,-7 z" fill="var(--white)"/></svg>
      555-014-2290
    </li>
    <li>
      <svg viewBox="0 0 18 18" aria-hidden="true"><rect x="1" y="4" width="16" height="11" rx="1.5" fill="var(--royal)"/><path d="M2,5 L9,10.5 L16,5" stroke="var(--white)" stroke-width="1.4" fill="none"/></svg>
      martin@harborlanejewelry.com
    </li>
    <li>
      <svg viewBox="0 0 18 18" aria-hidden="true"><circle cx="9" cy="9" r="7.5" fill="none" stroke="var(--royal)" stroke-width="1.6"/><ellipse cx="9" cy="9" rx="3.2" ry="7.5" fill="none" stroke="var(--royal)" stroke-width="1.2"/><path d="M1.5,9 H16.5 M3,5 H15 M3,13 H15" stroke="var(--royal)" stroke-width="1.1"/></svg>
      www.harborlanejewelry.com
    </li>
  </ul>
</section>

</body>
</html>
```